BRN website video quote promotion tiles

We are promoting vehicle leasing by video, which contains several quotation examples imported from the video. We must re-vamp the quotation tiles, contact boxes, and contact form. The first tile is generated from the video, so this must be a separate project. We are looking for a welcoming, professional flow and leave color choices to design with an emphasis on communication prompts, and additional prompts in the design would be welcome.

Target Market(s)

Any Customer interaction from the tile quotes, contact, call, message,

Industry/Entity Type

vehicle leasing

Coding

Coded - Design and coding required

Number of Pages Required

1 page

Colors

Designer to choose colors to be used in the design.

Requirements
Must have
• emphasis on point of contact and visual impact on quote tile excluding main one
Should not have
• changes to the quote structure as these imported from video pricing no changes to main image as this template which can addressed as separate project

```html
<!DOCTYPE html>
<html lang="en">
<head>
<meta charset="utf-8">
<title>Contact Details</title>
<link href="https://fonts.googleapis.com/css2?family=Montserrat:wght@400;500;600;700&display=swap" rel="stylesheet">
<style>
  :root {
    --bg: #f7f6f7;
    --bg-soft: #ecebec;
    --ink: #1f1f1f;
    --label: #222222;
    --placeholder: #9a9a9a;
    --icon: #9b9b9b;
    --field-border: #c9c9c9;
    --field-bg: #ffffff;
    --accent: #97c353;
    --white: #ffffff;
  }
  * { box-sizing: border-box; margin: 0; padding: 0; }
  html, body { width: 1200px; height: 723px; overflow: hidden; }
  body {
    font-family: "Montserrat", sans-serif;
    background:
      radial-gradient(circle at 330px 180px, var(--bg-soft) 0, transparent 260px),
      radial-gradient(circle at 900px 40px, var(--bg-soft) 0, transparent 220px),
      radial-gradient(circle at 1000px 520px, var(--bg-soft) 0, transparent 240px),
      var(--bg);
    position: relative;
    color: var(--ink);
  }
  .page-title {
    position: absolute;
    top: 30px; left: 0; width: 1200px;
    text-align: center;
    font-size: 41px;
    font-weight: 700;
    letter-spacing: 0.2px;
    color: var(--ink);
  }
  .message-illustration {
    position: absolute;
    left: 87px; top: 234px;
    width: 367px; height: 351px;
    background: var(--accent);
  }
  .contact-form {
    position: absolute;
    left: 536px; top: 140px;
    width: 552px;
  }
  .field-label {
    display: block;
    font-size: 15px;
    font-weight: 500;
    color: var(--label);
    margin-bottom: 10px;
  }
  .field {
    display: flex;
    align-items: center;
    gap: 10px;
    height: 49px;
    padding: 0 18px 0 21px;
    background: var(--field-bg);
    border: 1px solid var(--field-border);
    border-radius: 10px;
    margin-bottom: 26px;
    font-size: 13.5px;
    color: var(--placeholder);
  }
  .field svg { width: 14px; height: 14px; fill: var(--icon); flex: none; }
  .field--message {
    height: 127px;
    align-items: flex-start;
    padding-top: 14px;
    margin-bottom: 30px;
  }
  .submit-button {
    display: inline-flex;
    align-items: center;
    justify-content: center;
    gap: 10px;
    width: 140px; height: 39px;
    border-radius: 20px;
    background: var(--accent);
    color: var(--white);
    font-family: "Montserrat", sans-serif;
    font-size: 15px;
    font-weight: 600;
    border: none;
  }
  .submit-button svg { width: 16px; height: 16px; fill: var(--white); }
</style>
</head>
<body>
  <h1 class="page-title">Please Submit Your Contact Details</h1>

  <div class="message-illustration" role="img" aria-label="Green speech bubble illustration with an envelope and a red new-message badge"></div>

  <form class="contact-form">
    <span class="field-label">Your Name</span>
    <div class="field">
      <svg viewBox="0 0 16 16" aria-hidden="true"><circle cx="8" cy="4.5" r="3.5"/><path d="M1.5 16c0-4 2.8-6.5 6.5-6.5s6.5 2.5 6.5 6.5z"/></svg>
      <span>Your Name</span>
    </div>

    <span class="field-label">Email</span>
    <div class="field">
      <svg viewBox="0 0 16 16" aria-hidden="true"><path d="M0 3h16v1.2L8 9 0 4.2z"/><path d="M0 5.8l8 4.8 8-4.8V13H0z"/></svg>
      <span>Email</span>
    </div>

    <span class="field-label">Contact Number</span>
    <div class="field">
      <svg viewBox="0 0 16 16" aria-hidden="true"><path d="M0 3h16v1.2L8 9 0 4.2z"/><path d="M0 5.8l8 4.8 8-4.8V13H0z"/></svg>
      <span>Contact Number</span>
    </div>

    <span class="field-label">Message</span>
    <div class="field field--message">
      <span>Your Message</span>
    </div>

    <button type="button" class="submit-button">
      <svg viewBox="0 0 16 16" aria-hidden="true"><path d="M16 0L0 7l5 2 8-6-6 7.5V16l3-4 3.5 2z"/></svg>
      Submit
    </button>
  </form>
</body>
</html>
```